Business Card Design for Vintage Jazz

I am a vintage jazz band leader in New York City. My groups play the music of the 1920s, 1930s and 1940s. My website is morvalquist.com for more info on what I do.

I am looking for a two sided business card design that has the look and feel of a really nice business card from the 1930s. I need to convey with the design that my work has that vintage kind of class and style, but also conveys that we are fun and entertaining.

Most importantly it should make a bold staement. If Hal Denbrook had a card, what would it have looked like? I want a card that I feel confident will make an impact and will let people know that my work is te the top that NYC has to offer in vintage jazz..

Note that I have only decided to avoid the "committed payment" option as I have not used this service before. Assuming that I get quality work I will select a design from those presented.

Target Market(s)

people who want to hire my band for events, media, and new fans of the band

Industry/Entity Type

Performing Art

Contact Information for Business Card

Definitely a matte finish, possibly a sort of old style of paper with that brown tint? definitely a thick card.

Requirements
Must have
• FRONT
• My name: Tobin Vashley
• What I do: Bandleader, Guitarist, Vocalist, Songwriter
• Contact Details: morvalquist.com tobin@morvalquist.com 646-555-0148
• BACK
• My Social Media Links:
• facebook.morvalquist.com
• twitter, instagram, linkedin: morvalquist
• I'm also including a photo image I would like to use. The photo's background is not needed, and to be honest isn't really desireable. Just looking to use the image of me.
Nice to have
• I'm attaching which could be used as is, omitted from the card, or altered maybe with text going around the outside of the circle or in some other way. It may need some clean up to the edges of the lettering as we only use it for the website thumbnail.
• If there's space I'd like to include the text "join our mailing list for a free song download: freesong.morvalquist.com" If not perhaps just "Download a Free Song at: freesong.morvalquist.com - something to this end.
Should not have
• anything cartoony. Don't think retro 90s's vision of the swing era, think actual swing era!
• anything modern. Got to look old school
• Try to avoid dark backgrounds. Since we often play in bars and clubs where it is dar, a d
• avoid script fonts.

```html
<!DOCTYPE html>
<html lang="en">
<head>
<meta charset="utf-8">
<title>Tobin Vashley – Business Card</title>
<link href="https://fonts.googleapis.com/css2?family=Source+Sans+3:ital,wght@0,400;0,600;1,400;1,600&display=swap" rel="stylesheet">
<style>
  :root {
    --backdrop: #2b2b2b;
    --card: #ffffff;
    --ink: #111111;
    --ink-soft: #555555;
    --ink-muted: #4a4a4a;
    --band: #050505;
    --on-band: #f2f2f2;
    --rule: #333333;
    --photo-light: #d8d8d8;
    --photo-dark: #1c1c1c;
  }
  * { box-sizing: border-box; margin: 0; padding: 0; }
  html, body {
    width: 1200px; height: 886px; overflow: hidden;
    background: var(--backdrop);
    font-family: "Source Sans 3", Arial, sans-serif;
  }
  .card {
    position: absolute;
    width: 565px; height: 322px;
    background: var(--card);
    border-radius: 16px;
    overflow: hidden;
    box-shadow: 0 6px 18px rgba(0,0,0,0.45);
  }
  .card--front { left: 315px; top: 102px; }
  .card--back  { left: 312px; top: 460px; }

  /* Front */
  .front__band {
    position: absolute; left: 0; right: 0; top: 197px; bottom: 0;
    background: var(--band);
  }
  .front__portrait {
    position: absolute; left: 253px; top: 0; width: 312px; height: 322px;
    background: linear-gradient(180deg, var(--photo-light) 0%, #9a9a9a 25%, var(--photo-dark) 60%, #2e2e2e 100%);
    border-top-left-radius: 60px;
  }
  .front__name {
    position: absolute; left: 38px; top: 33px;
    font-size: 20px; font-weight: 600; color: var(--ink);
  }
  .front__roles {
    position: absolute; left: 38px; top: 59px;
    font-size: 16px; line-height: 21px; color: var(--ink-soft);
  }
  .contact {
    position: absolute; left: 38px; top: 230px;
    list-style: none; color: var(--on-band); font-size: 16px;
  }
  .contact li { display: flex; align-items: center; height: 22px; }
  .contact svg { width: 14px; height: 14px; margin-right: 7px; flex: none; }

  /* Back */
  .back__mark {
    position: absolute; left: 0; right: 0; top: 98px;
    display: flex; align-items: center; justify-content: center; gap: 14px;
  }
  .back__mark-dot {
    width: 60px; height: 60px; border-radius: 50%; background: var(--ink);
  }
  .back__mark-name { font-size: 30px; font-weight: 600; color: var(--ink); }
  .back__rule {
    position: absolute; left: 31px; right: 29px; top: 240px;
    border-top: 1.5px solid var(--rule);
  }
  .social {
    position: absolute; left: 31px; top: 251px;
    list-style: none; font-size: 16px; color: var(--ink-muted);
  }
  .social li { display: flex; align-items: center; height: 26px; }
  .social__dot {
    width: 21px; height: 21px; border-radius: 50%; background: var(--ink);
    margin-right: 8px; flex: none;
  }
  .freesong {
    position: absolute; right: 29px; top: 253px; text-align: right;
    font-style: italic; color: var(--ink-muted); line-height: 21px;
  }
  .freesong__label { font-size: 16px; }
  .freesong__url { font-size: 16px; font-weight: 600; }
</style>
</head>
<body>

<section class="card card--front" aria-label="Card front">
  <div class="front__band"></div>
  <div class="front__portrait" role="img" aria-label="Portrait of Tobin Vashley in a blazer and cravat, tipping a straw boater hat"></div>
  <h1 class="front__name">Tobin Vashley</h1>
  <p class="front__roles">Bandleader, Guitarist<br>Vocalist, Songwriter</p>
  <ul class="contact">
    <li>
      <svg viewBox="0 0 14 14" aria-hidden="true"><rect x="3" y="0.5" width="8" height="13" rx="1.5" fill="none" stroke="currentColor" stroke-width="1.5"/><rect x="4.5" y="2.5" width="5" height="7" fill="currentColor"/></svg>
      646-555-0148
    </li>
    <li>
      <svg viewBox="0 0 14 14" aria-hidden="true"><rect x="1" y="3" width="12" height="8" fill="currentColor"/><path d="M1 3 L7 8 L13 3" fill="none" stroke="#050505" stroke-width="1.2"/></svg>
      tobin@morvalquist.com
    </li>
    <li>
      <svg viewBox="0 0 14 14" aria-hidden="true"><circle cx="7" cy="7" r="6.3" fill="currentColor"/><path d="M1 7 H13 M7 1 C4 4 4 10 7 13 M7 1 C10 4 10 10 7 13" fill="none" stroke="#050505" stroke-width="1"/></svg>
      morvalquist.com
    </li>
  </ul>
</section>

<section class="card card--back" aria-label="Card back">
  <div class="back__mark">
    <span class="back__mark-dot"></span>
    <span class="back__mark-name">Tobin Vashley</span>
  </div>
  <div class="back__rule"></div>
  <ul class="social">
    <li><span class="social__dot"></span>morvalquist.com</li>
    <li><span class="social__dot"></span>morvalquist</li>
  </ul>
  <div class="freesong">
    <p class="freesong__label">Download a Free Song at:</p>
    <p class="freesong__url">freesong.morvalquist.com</p>
  </div>
</section>

</body>
</html>
```